Kestrelway Financial Plans

I am looking for a complete resdesign of my small financial presentation. This is a Word Doc/PDF that I print off when meeting with people in private. I often present my "two pager" that I have been using for years and years. It tells them the basics of what I do, how I help people and foundational financial principles.

I have recently gone out on my own in business and have completely rebranded. This presentation is my most used tool, so it is the first of many things I would like to redo. I am hoping it will somehow coordinate with the colors of my business, not necessarily the EXACT same 3 colors everywhere, but have the design colors compliment.

I've uploaded all my logo designs, as well as the current "two-pager". I am not against it going to 3 pages if needed. As it will still land on 2 pages with duplex printing.

It has always been VERY simple. I am wanting it built into a more professional and design specific format, to show off my branding, without being over cluttered.

I am completely open to ANY graphics changes. Obviously some are very novice, the house on the last page has always been overly simplified.

```html
<!DOCTYPE html>
<html lang="en">
<head>
<meta charset="utf-8">
<title>Kestrelway Financial Plans – Client Overview</title>
<link rel="stylesheet" href="https://fonts.googleapis.com/css2?family=Roboto:ital,wght@0,400;0,500;0,700;0,900;1,400&display=swap">
<style>
:root{
  --green:#23a136;
  --navy:#0e1a2a;
  --slate:#6c7279;
  --maroon:#6e0f1c;
  --backdrop:#4a4a4a;
  --ink:#1c1c1c;
  --muted:#3f3f3f;
  --rule:#e2e2e2;
  --partner:#cfe0f4;
}
*{box-sizing:border-box;margin:0;padding:0}
html,body{width:1200px;height:2987px;overflow:hidden}
body{background:var(--backdrop);font-family:'Roboto',sans-serif;color:var(--ink);position:relative}
.abs{position:absolute}
.page{position:absolute;left:59px;width:1082px;background:#fff;overflow:hidden}
.page--one{top:59px;height:1402px}
.page--two{top:1526px;height:1400px;background:linear-gradient(160deg,#fafafa 0%,#f1f1f1 45%,#fbfbfb 70%,#ececec 100%)}

/* brand header */
.brand-box{position:absolute;left:20px;top:20px;width:1041px;height:160px;border:1.5px solid var(--green);border-radius:14px}
.brand-name{position:absolute;left:0;right:0;top:28px;text-align:center;font-weight:700;font-size:60px;letter-spacing:1px;color:var(--navy);line-height:64px}
.brand-sub{position:absolute;left:0;right:0;top:100px;display:flex;justify-content:center;align-items:center;gap:18px;font-weight:700;font-size:22px;letter-spacing:4px;color:var(--navy)}
.brand-sub::before,.brand-sub::after{content:"";width:56px;height:4px;background:var(--navy)}

/* challenge */
.challenge-title{position:absolute;left:31px;top:683px;transform:rotate(-90deg);transform-origin:0 0;width:446px;font-weight:900;font-size:34px;color:var(--navy);white-space:nowrap;line-height:30px}
.challenge-rule{position:absolute;left:43px;top:706px;width:3px;height:140px;background:var(--green)}
.topic-pill{position:absolute;left:92px;width:240px;height:78px;border-radius:39px;color:#fff;display:flex;align-items:center;gap:22px;padding-left:36px;font-weight:500;font-size:23px;letter-spacing:.5px}
.topic-pill svg{width:26px;height:26px}
.topic-pill--savings{top:231px;background:var(--green)}
.topic-pill--debt{top:392px;background:var(--slate)}
.topic-pill--insurance{top:552px;background:var(--navy)}
.fact-list{position:absolute;left:364px;width:698px;list-style:none;font-size:14.6px;line-height:33px;color:var(--muted)}
.fact-list li{position:relative;padding-left:28px}
.fact-list li::before,.card-points li::before{content:"";position:absolute;left:0;top:11px;width:11px;height:11px;border:2px solid var(--green);border-radius:50%;background:radial-gradient(circle,var(--green) 0 2px,transparent 2.6px)}

/* who we are */
.mission{position:absolute;left:0;top:700px;width:1082px;height:460px}
.mission-heading{position:absolute;left:0;right:0;top:743px;text-align:center;color:#fff;font-weight:900;font-size:35px;line-height:41px}
.service{position:absolute;width:180px;text-align:center}
.service-disc{width:106px;height:106px;margin:0 auto;border-radius:50%;background:#fff;display:flex;align-items:center;justify-content:center}
.service-disc svg{width:62px;height:62px}
.service-label{margin-top:12px;color:#fff;font-weight:700;font-size:15px;line-height:18px}
.awareness-btn{position:absolute;left:368px;top:1081px;width:346px;height:57px;border-radius:29px;background:var(--green);color:#fff;font-weight:700;font-size:18px;display:flex;align-items:center;justify-content:center}

/* how */
.how-heading{position:absolute;left:115px;top:1230px;font-weight:900;font-size:35px;line-height:41px;color:var(--navy)}
.flow-arrow{position:absolute;width:34px;text-align:center}
.flow-arrow svg{width:34px;height:16px}
.flow-arrow span{display:block;font-size:7px;font-style:italic;font-weight:700;color:#333}
.goal-row{position:absolute;left:544px;width:110px;height:26px;background:#fff;border-radius:6px;box-shadow:0 1px 5px rgba(0,0,0,.15);display:flex;align-items:center;gap:6px;padding-left:3px;font-size:7px;font-style:italic;color:#777}
.goal-row i{width:20px;height:20px;border-radius:50%;background:var(--green);flex:none}
.partner{position:absolute;height:27px;border-radius:6px;background:var(--partner)}
.page-foot{position:absolute;left:0;bottom:0;width:1082px;height:7px;background:var(--green)}

/* rule of 72 */
.section-title{position:absolute;left:78px;top:40px;font-weight:900;font-size:33px;color:var(--ink)}
.rule-table{position:absolute;width:286px;background:#fff;border-radius:34px 34px 28px 28px;box-shadow:0 6px 18px rgba(0,0,0,.08);overflow:hidden}
.rule-head{height:67px;border-radius:34px;background:var(--green);color:#fff;display:flex;justify-content:space-between;align-items:center;padding:0 30px 0 42px;font-size:21px}
.rule-head b{font-weight:700}
.rule-row{height:72px;display:grid;grid-template-columns:144px 142px;border-top:1px solid var(--rule);font-size:21px;color:var(--muted);align-items:center}
.rule-row:first-of-type{border-top:none}
.rule-row span:first-child{padding-left:46px}
.rule-row span:last-child{height:100%;display:flex;align-items:center;justify-content:flex-end;padding-right:31px;border-left:1px solid var(--rule)}
.rule-caption{position:absolute;font-weight:500;font-size:16px;color:var(--ink);white-space:pre}

.account-card{position:absolute;left:403px;width:607px;border-radius:22px;color:#fff}
.account-card--navy{background:var(--navy)}
.account-card--green{background:var(--green)}
.card-icon{position:absolute;left:30px;width:62px;height:62px;border-radius:50%;display:flex;align-items:center;justify-content:center}
.card-icon svg{width:32px;height:32px}
.card-title{position:absolute;left:121px;font-weight:700;font-size:23px;line-height:28px}
.card-points{position:absolute;left:121px;list-style:none;font-size:14.6px;line-height:25.5px}
.card-points li{position:relative;padding-left:26px}
.card-points li::before{top:7px;border-color:#fff;background:radial-gradient(circle,#fff 0 2px,transparent 2.6px)}
.card-badge{position:absolute;right:29px;height:30px;border-radius:15px;font-weight:700;font-size:15px;display:flex;align-items:center;justify-content:center;color:#fff}
.side-notes{position:absolute;left:79px;font-weight:700;font-size:15px;line-height:27px;color:var(--ink)}
.side-rule{position:absolute;left:79px;top:1261px;width:324px;height:1px;background:#777}
</style>
</head>
<body>

<section class="page page--one">
  <header class="brand-box">
    <div class="brand-name">KESTRELWAY</div>
    <div class="brand-sub">FINANCIAL PLANS</div>
  </header>

  <h2 class="challenge-title">THE FINANCIAL CHALLENGE</h2>
  <div class="challenge-rule"></div>

  <div class="topic-pill topic-pill--savings">
    <svg viewBox="0 0 24 24"><path d="M11 2a10 10 0 1 0 11 11H11z" fill="#fff"/><path d="M13 0v11h11A11 11 0 0 0 13 0z" fill="#fff"/></svg>SAVINGS
  </div>
  <div class="topic-pill topic-pill--debt">
    <svg viewBox="0 0 24 24"><path d="M2 3h9l11 11-8 8L3 11z" fill="#fff"/><circle cx="7" cy="7" r="2" fill="#6c7279"/></svg>DEBT
  </div>
  <div class="topic-pill topic-pill--insurance">
    <svg viewBox="0 0 24 24" fill="none" stroke="#fff" stroke-width="3"><path d="M4 11V7h15M15 3l4 4-4 4M20 13v4H5M9 21l-4-4 4-4"/></svg>INSURANCE
  </div>

  <ul class="fact-list" style="top:221px">
    <li>49% of canadian employees are living paycheque to paycheque. 25% of Canadians are unable to cover an unexpected $500 expense-national stats bureau (Feb 2023)</li>
    <li>25% of canadians need to access their retirement savings early. 20% of Canadians have no savings. 39% of canadians aged 55-65 have less Than $5,000 in savings. -federal finance office (June 2023)</li>
  </ul>
  <ul class="fact-list" style="top:382px">
    <li>The average canadian has $22,131 in consumer debt. Which excludes mortgages.-ledgerline credit (Aug 2024)</li>
    <li>Over 55% of canadians hold credit card debt and the total canadian household debt has increased to $2.52trillion, including consumer credit, mortgage and non-mortgage loans. -national lenders council (Aug 2024)</li>
  </ul>
  <ul class="fact-list" style="top:543px">
    <li>45% of canadians do not have individual life insurance coverage, but 48% say their families would face financial trouble within 6 months of losing someone.-insurewise research intl. (Apr 2023)</li>
    <li>2-in-5 canadians (43% women / 44% men) will be diagosed with a form of cancer or other critical illness during their lifetime. Every 7 seconds.-wellness data canada (June 2024)</li>
  </ul>

  <svg class="abs" style="left:0;top:0" width="1082" height="1402" viewBox="59 59 1082 1402" aria-hidden="true">
    <ellipse cx="600" cy="1007" rx="541" ry="219" fill="var(--navy)"/>
    <path d="M255 817 Q600 721 945 817 Q600 987 255 817Z" fill="var(--green)"/>
  </svg>
  <h2 class="mission-heading">WHO ARE WE AND WHAT<br>DO WE DO?</h2>

  <div class="service" style="left:26px;top:871px">
    <div class="service-disc"><svg viewBox="0 0 64 64"><rect x="6" y="22" width="50" height="30" rx="3" fill="var(--green)"/><rect x="10" y="16" width="44" height="6" fill="var(--green)"/><circle cx="31" cy="37" r="7" fill="#fff"/><circle cx="15" cy="37" r="3" fill="#fff"/><circle cx="47" cy="37" r="3" fill="#fff"/></svg></div>
    <div class="service-label">CASH FLOW</div>
  </div>
  <div class="service" style="left:192px;top:909px">
    <div class="service-disc"><svg viewBox="0 0 64 64"><path d="M6 32a26 24 0 0 1 52 0z" fill="var(--green)"/><path d="M32 32v18a5 5 0 0 1-10 0" fill="none" stroke="var(--green)" stroke-width="4"/><rect x="30" y="4" width="4" height="6" fill="var(--green)"/></svg></div>
    <div class="service-label">CASH FLOW PROTECTION</div>
  </div>
  <div class="service" style="left:377px;top:871px">
    <div class="service-disc"><svg viewBox="0 0 64 64"><rect x="6" y="14" width="48" height="36" rx="4" fill="var(--green)"/><rect x="6" y="22" width="48" height="6" fill="#fff"/><rect x="12" y="36" width="18" height="4" fill="#fff"/><path d="M10 56 56 8" stroke="#fff" stroke-width="7"/><path d="M10 56 56 8" stroke="var(--green)" stroke-width="3"/></svg></div>
    <div class="service-label">DEBT MANAGEMENT</div>
  </div>
  <div class="service" style="left:557px;top:909px">
    <div class="service-disc"><svg viewBox="0 0 64 64"><path d="M4 18h36v28H4z" fill="var(--green)"/><path d="M40 26h12l8 10v10H40z" fill="var(--green)"/><circle cx="14" cy="48" r="6" fill="var(--green)" stroke="#fff" stroke-width="2"/><circle cx="48" cy="48" r="6" fill="var(--green)" stroke="#fff" stroke-width="2"/><path d="M22 24v16M14 32h16" stroke="#fff" stroke-width="4"/><rect x="44" y="29" width="8" height="6" fill="#fff"/></svg></div>
    <div class="service-label">EMERGENCY FUND</div>
  </div>
  <div class="service" style="left:718px;top:871px">
    <div class="service-disc"><svg viewBox="0 0 64 64"><ellipse cx="30" cy="34" rx="22" ry="16" fill="var(--green)"/><rect x="16" y="44" width="6" height="10" fill="var(--green)"/><rect x="36" y="44" width="6" height="10" fill="var(--green)"/><rect x="24" y="16" width="12" height="4" fill="var(--green)"/><circle cx="56" cy="32" r="4" fill="var(--green)"/></svg></div>
    <div class="service-label">BUILD WEALTH</div>
  </div>
  <div class="service" style="left:875px;top:909px">
    <div class="service-disc"><svg viewBox="0 0 64 64"><rect x="10" y="8" width="44" height="46" rx="4" fill="none" stroke="var(--green)" stroke-width="5"/><rect x="17" y="15" width="30" height="32" fill="none" stroke="var(--green)" stroke-width="3"/><path d="M41 24v14" stroke="var(--green)" stroke-width="3"/><circle cx="28" cy="31" r="4" fill="none" stroke="var(--green)" stroke-width="2"/><rect x="14" y="54" width="6" height="4" fill="var(--green)"/><rect x="44" y="54" width="6" height="4" fill="var(--green)"/></svg></div>
    <div class="service-label">PRESERVE</div>
  </div>

  <div class="awareness-btn">EDUCATION &amp; AWARENESS</div>

  <h2 class="how-heading">HOW<br>ARE WE<br>DOING IT?</h2>

  <svg class="abs" style="left:337px;top:1233px" width="120" height="120" viewBox="0 0 120 120" role="img" aria-label="Pie chart of income: living expenses, taxes and debt">
    <circle cx="60" cy="60" r="60" fill="var(--maroon)"/>
    <path d="M60 0v120M60 60h60" stroke="#fff" stroke-width="3"/>
    <g fill="#fff" font-family="Roboto,sans-serif" font-size="9" text-anchor="middle">
      <text x="32" y="57">Living</text><text x="32" y="69">Expenses</text>
      <text x="90" y="43">Taxes</text><text x="90" y="93">Debt</text>
    </g>
  </svg>

  <div class="flow-arrow" style="left:481px;top:1277px"><svg viewBox="0 0 34 16"><path d="M1 8h31M24 1l8 7-8 7" fill="none" stroke="#222" stroke-width="2"/></svg><span>Savings</span></div>
  <div class="goal-row" style="top:1230px"><i></i>Retirement Savings</div>
  <div class="goal-row" style="top:1264px"><i></i>Children Education</div>
  <div class="goal-row" style="top:1297px"><i></i>Proper Protection</div>
  <div class="goal-row" style="top:1331px"><i></i>Freedom From Debt</div>
  <div class="flow-arrow" style="left:681px;top:1277px"><svg viewBox="0 0 34 16"><path d="M1 8h31M24 1l8 7-8 7" fill="none" stroke="#222" stroke-width="2"/></svg></div>

  <div class="partner" style="left:740px;top:1212px;width:79px"></div>
  <div class="partner" style="left:823px;top:1212px;width:84px"></div>
  <div class="partner" style="left:740px;top:1244px;width:79px"></div>
  <div class="partner" style="left:823px;top:1244px;width:84px"></div>
  <div class="partner" style="left:740px;top:1277px;width:79px"></div>
  <div class="partner" style="left:823px;top:1277px;width:84px"></div>
  <div class="partner" style="left:740px;top:1309px;width:79px"></div>
  <div class="partner" style="left:823px;top:1309px;width:84px"></div>
  <div class="partner" style="left:740px;top:1340px;width:79px"></div>
  <div class="partner" style="left:823px;top:1340px;width:84px"></div>

  <div class="flow-arrow" style="left:937px;top:1277px"><svg viewBox="0 0 34 16"><path d="M1 8h31M24 1l8 7-8 7" fill="none" stroke="#222" stroke-width="2"/></svg><span>Pay Us</span></div>

  <div class="page-foot"></div>
</section>

<section class="page page--two">
  <h2 class="section-title">RULE OF 72</h2>

  <div class="rule-table" style="left:79px;top:109px">
    <div class="rule-head"><b>AGE</b><span>4%</span></div>
    <div class="rule-row"><span>29</span><span>$ 10,000</span></div>
    <div class="rule-row"><span>47</span><span>$ 20,000</span></div>
    <div class="rule-row"><span>65</span><span>$ 40,000</span></div>
  </div>
  <div class="rule-caption" style="left:78px;top:420px">MONEY DOUBLES  EVERY 18 YEARS</div>

  <div class="rule-table" style="left:400px;top:109px">
    <div class="rule-head"><b>AGE</b><span>6%</span></div>
    <div class="rule-row"><span>29</span><span>$ 10,000</span></div>
    <div class="rule-row"><span>41</span><span>$ 20,000</span></div>
    <div class="rule-row"><span>53</span><span>$ 40,000</span></div>
    <div class="rule-row"><span>65</span><span>$ 80,000</span></div>
  </div>
  <div class="rule-caption" style="left:413px;top:495px">MONEY DOUBLES  EVERY 12 YEARS</div>

  <div class="rule-table" style="left:722px;top:109px">
    <div class="rule-head"><b>AGE</b><span>8%</span></div>
    <div class="rule-row"><span>29</span><span>$ 10,000</span></div>
    <div class="rule-row"><span>38</span><span>$ 20,000</span></div>
    <div class="rule-row"><span>47</span><span>$ 40,000</span></div>
    <div class="rule-row"><span>56</span><span>$ 80,000</span></div>
    <div class="rule-row"><span>65</span><span>$ 160,000</span></div>
  </div>
  <div class="rule-caption" style="left:741px;top:572px">MONEY DOUBLES  EVERY 9 YEARS</div>

  <div class="rule-table" style="left:79px;top:468px">
    <div class="rule-head"><b>AGE</b><span>12%</span></div>
    <div class="rule-row"><span>29</span><span>$ 10,000</span></div>
    <div class="rule-row"><span>35</span><span>$ 20,000</span></div>
    <div class="rule-row"><span>41</span><span>$ 40,000</span></div>
    <div class="rule-row"><span>47</span><span>$ 80,000</span></div>
    <div class="rule-row"><span>53</span><span>$ 160,000</span></div>
    <div class="rule-row"><span>59</span><span>$ 160,000</span></div>
    <div class="rule-row"><span>65</span><span>$ 160,000</span></div>
  </div>
  <div class="rule-caption" style="left:98px;top:1077px">MONEY DOUBLES  EVERY 6 YEARS</div>

  <div class="account-card account-card--navy" style="top:633px;height:148px">
    <div class="card-icon" style="top:36px;background:var(--green)"><svg viewBox="0 0 32 32"><path d="M16 4 2 16h4v12h8v-8h4v8h8V16h4z" fill="#fff"/></svg></div>
    <div class="card-title" style="top:31px">HOME</div>
    <ul class="card-points" style="top:68px"><li>Partner with mortage brokers for best rates.</li><li>Mortage insurance alternatives</li></ul>
    <div class="card-badge" style="top:37px;width:89px;background:var(--green)">SELL</div>
  </div>

  <div class="account-card account-card--green" style="top:806px;height:148px">
    <div class="card-icon" style="top:36px;background:var(--navy)"><svg viewBox="0 0 32 32"><path d="M8 3h12l6 6v20H8z" fill="#fff"/><circle cx="13" cy="20" r="6" fill="var(--navy)"/><path d="M10 23l6-6" stroke="#fff" stroke-width="1.6"/><path d="M19 12h5M19 16h5" stroke="var(--navy)" stroke-width="2"/></svg></div>
    <div class="card-title" style="top:37px">RRSP</div>
    <ul class="card-points" style="top:73px"><li>Tax Deduction</li><li>Tax Deferred</li></ul>
    <div class="card-badge" style="top:37px;width:109px;background:var(--navy)">100% TAX</div>
  </div>

  <div class="account-card account-card--navy" style="top:978px;height:188px">
    <div class="card-icon" style="top:36px;background:var(--green)"><svg viewBox="0 0 32 32"><path d="M5 26h4v-7H5zM11 26h4v-10h-4zM17 26h4v-13h-4zM23 26h4V9h-4z" fill="#fff"/><path d="M4 15 14 8l5 3 8-6M22 5h5v5" fill="none" stroke="#fff" stroke-width="2"/></svg></div>
    <div class="card-title" style="top:27px">TFSA</div>
    <ul class="card-points" style="top:63px"><li>No Tax Deductions</li><li>Tax Free Growth</li><li>2009 - $95,000</li><li>Limit 2023-$7,000/YR</li></ul>
    <div class="card-badge" style="top:32px;width:87px;background:var(--green)">0% TAX</div>
  </div>

  <div class="account-card account-card--green" style="top:1190px;height:154px">
    <div class="card-icon" style="top:36px;background:var(--navy)"><svg viewBox="0 0 32 32"><path d="M12 4h8l-2 5h-4z" fill="#fff"/><path d="M13 10h6c6 4 9 9 9 13 0 4-3 6-12 6S4 27 4 23c0-4 3-9 9-13z" fill="#fff"/><text x="16" y="25" text-anchor="middle" font-family="Roboto,sans-serif" font-weight="700" font-size="11" fill="var(--navy)">$</text></svg></div>
    <div class="card-title" style="top:33px">PERM LIFE</div>
    <ul class="card-points" style="top:68px"><li>No Tax Deduction</li><li>Qualify</li><li>Tax Deferred Growth</li></ul>
    <div class="card-badge" style="top:27px;width:87px;background:var(--navy)">0% TAX</div>
  </div>

  <div class="side-notes" style="top:1192px">LIFE INSURANCE ILLNESS<br>CRITICAL/DISABILITY</div>
  <div class="side-rule"></div>
  <div class="side-notes" style="top:1281px">DEBT MANAGEMENT<br>CASH FLOW</div>
</section>

</body>
</html>
```